Broschüre
Zielgruppe
Die T.O.R.K. Lumen Holding GmbH ist ein inhabergeführtes Immobilienunternehmen mit Sitz in Moers. Wir sind spezialisiert auf den direkten Ankauf von Mehrfamilienhäusern, Wohnanlagen und größeren Wohnimmobilien in Nordrhein-Westfalen. Unser Schwerpunkt liegt auf einer schnellen, diskreten und unbürokratischen Abwicklung – vom ersten Kontakt bis zum notariellen Abschluss. Wir kaufen Objekte in jedem Zustand, ob vermietet, leerstehend oder sanierungsbedürftig.
Wer ist Deine Zielgruppe?
• Institutionelle Eigentümer z.b. Wohnungsunternehmen und Investoren, die Bestände veräußern wollen
Aufgabenstellung
• Corporate Identity: Seriös, modern, vertrauenswürdig. Die Broschüre soll unsere Professionalität und Diskretion betonen.
• Farben: Anlehnung an die Unternehmensfarben der T.O.R.K. Lumen Holding GmbH (dezent, elegant, z. B. dunkles Blau, Grau, Weiß; ggf. Akzentfarbe Gold oder ein warmes Gelb).
• Schriftarten: Gut lesbar, modern, ohne verschnörkelte Fonts.
• Format: Hochformat DIN A4, 4–8 Seiten, übersichtlich und klar strukturiert.
• Bildsprache: Hochwertige Immobilienbilder, urbane Aufnahmen aus NRW, Detailfotos (z. B. Architektur, Gebäudeansichten) sowie emotionale Motive, die Vertrauen und Sicherheit vermitteln.
• Ton & Stil: Seriös, diskret, aber sympathisch – nicht zu werblich, sondern lösungsorientiert.
• Logo: Unser Firmenlogo muss auf dem Titel und der Rückseite gut sichtbar platziert sein.

```html
<!DOCTYPE html>
<html lang="en">
<head>
<meta charset="utf-8">
<title>T.O.R.K. Lumen Holding GmbH – Brochure</title>
<link rel="stylesheet" href="https://fonts.googleapis.com/css2?family=Barlow:wght@500;600;700&family=Source+Sans+3:wght@400;500&display=swap">
<style>
  :root {
    --navy: #24304a;
    --paper: #ecebe7;
    --backdrop: #d4d4d4;
    --gold: #b1995c;
    --ink: #1f2a40;
    --text: #2b2f38;
    --muted-light: #c9cfdb;
    --sky-top: #c3d0dc;
    --sky-bottom: #dfe4e8;
    --facade: #a9a49b;
    --facade-dark: #77746f;
  }
  * { box-sizing: border-box; margin: 0; padding: 0; }
  html, body { width: 800px; height: 1200px; overflow: hidden; }
  body { background: var(--backdrop); position: relative; font-family: "Source Sans 3", sans-serif; color: var(--text); }

  .page { position: absolute; overflow: hidden; box-shadow: 0 2px 6px rgba(0,0,0,.18); }
  .photo { position: absolute; left: 0; width: 100%; }
  .photo--building { background: linear-gradient(180deg, var(--sky-top) 0%, var(--sky-bottom) 35%, var(--facade) 36%, var(--facade-dark) 100%); }

  /* cover */
  .cover { left: 120px; top: 0; width: 273px; height: 451px; }
  .cover__brand { position: absolute; inset: 0 0 auto 0; height: 215px; background: var(--navy);
    display: flex; flex-direction: column; align-items: center; justify-content: center; gap: 8px; }
  .cover__mark { width: 14px; height: 14px; background: #ffffff; }
  .cover__name { font-family: "Barlow", sans-serif; font-weight: 600; color: #ffffff; font-size: 15px;
    letter-spacing: .06em; text-align: center; line-height: 1.25; }
  .cover .photo { top: 215px; height: 236px; }

  .title-page { left: 405px; top: 0; width: 276px; height: 451px; }
  .title-page .photo { top: 0; height: 276px; }
  .title-page__band { position: absolute; top: 276px; left: 0; right: 0; bottom: 0; background: var(--navy); }
  .title-page__heading { position: absolute; left: 28px; top: 304px; font-family: "Barlow", sans-serif;
    font-weight: 700; font-size: 32px; line-height: 1.16; color: #ffffff; letter-spacing: .01em; }

  /* inner left */
  .inner-left { left: 70px; top: 483px; width: 324px; height: 717px; background: var(--paper); }
  .section-heading { font-family: "Barlow", sans-serif; font-weight: 700; color: var(--ink);
    font-size: 25px; line-height: 1.17; letter-spacing: .01em; }
  .about { position: absolute; left: 32px; top: 30px; right: 20px; }
  .about p { font-size: 12px; line-height: 1.5; margin-top: 20px; }
  .about p + p { margin-top: 16px; }
  .inner-left .photo { top: 269px; height: 292px; }
  .properties { position: absolute; left: 32px; top: 584px; }
  .properties ul { list-style: none; margin-top: 16px; }
  .properties li { font-size: 13px; margin-bottom: 9px; padding-left: 17px; position: relative; }
  .properties li::before { content: ""; position: absolute; left: 2px; top: 7px; width: 4px; height: 4px; border-radius: 50%; background: var(--ink); }

  /* inner right */
  .inner-right { left: 405px; top: 483px; width: 325px; height: 717px; background: var(--paper); }
  .process { position: absolute; left: 32px; top: 30px; }
  .process__steps { list-style: none; margin-top: 30px; }
  .process__step { display: flex; align-items: center; gap: 12px; height: 26px; font-size: 13px; font-weight: 500; color: var(--ink); position: relative; }
  .process__step + .process__step { margin-top: 20.5px; }
  .process__step + .process__step::before { content: ""; position: absolute; left: 12px; top: -16px; width: 2px; height: 10px; background: var(--gold); }
  .process__num { width: 26px; height: 26px; border-radius: 50%; background: var(--gold); color: #ffffff;
    display: flex; align-items: center; justify-content: center; font-size: 13px; }
  .process__photo { position: absolute; left: 204px; top: 64px; width: 121px; height: 250px;
    background: linear-gradient(180deg, var(--paper) 0%, #b7b9bd 25%, #8d9096 100%); }

  .why { position: absolute; left: 0; top: 314px; width: 100%; height: 271px; background: var(--navy); padding: 34px 0 0 32px; }
  .why .section-heading { color: #ffffff; font-size: 24px; }
  .why__list { list-style: none; margin-top: 20px; }
  .why__item { display: flex; gap: 16px; align-items: flex-start; }
  .why__item + .why__item { margin-top: 19px; }
  .why__icon { width: 32px; height: 32px; border-radius: 50%; background: var(--gold); flex: none; margin-top: 2px;
    display: flex; align-items: center; justify-content: center; }
  .why__title { font-family: "Barlow", sans-serif; font-weight: 500; color: #ffffff; font-size: 15px; }
  .why__text { font-size: 10px; color: var(--muted-light); margin-top: 5px; }

  .contact { position: absolute; left: 32px; top: 612px; }
  .contact .section-heading { font-size: 24px; }
  .contact__list { list-style: none; margin-top: 18px; }
  .contact__item { display: flex; align-items: center; gap: 14px; font-size: 14px; color: var(--ink); }
  .contact__item + .contact__item { margin-top: 10px; }
  .contact__icon { width: 18px; height: 18px; border-radius: 50%; background: var(--gold); display: flex; align-items: center; justify-content: center; }
</style>
</head>
<body>

  <section class="page cover">
    <div class="cover__brand">
      <span class="cover__mark"></span>
      <div class="cover__name">T.O.R.K. LUMEN<br>HOLDING GMBH</div>
    </div>
    <div class="photo photo--building" role="img" aria-label="Modern light-coloured apartment building with balconies against a pale sky"></div>
  </section>

  <section class="page title-page">
    <div class="photo photo--building" role="img" aria-label="Tall modern residential building with recessed balconies, seen from below"></div>
    <div class="title-page__band"></div>
    <h1 class="title-page__heading">INVESTMENT<br>IN RESIDENTIAL<br>PROPERTIES</h1>
  </section>

  <section class="page inner-left">
    <div class="about">
      <h2 class="section-heading">ABOUT T.O.R.K. LUMEN<br>HOLDING GMBH</h2>
      <p>A family run real estate firm based in Moers, specialising in the direct purchase of multi-family houses, residential complexes, and larger residential properties in North Rhine.</p>
      <p>We buy properties in any condition, whether let, vacant or in need of renovation across the region.</p>
    </div>
    <div class="photo photo--building" role="img" aria-label="Grey multi-storey residential building with balconies in an urban setting" style="top:269px;height:292px;"></div>
    <div class="properties">
      <h2 class="section-heading">PROPERTIES WE BUY</h2>
      <ul>
        <li>Apartment Buildings</li>
        <li>Residential Complexes</li>
        <li>Large Residential Properties</li>
      </ul>
    </div>
  </section>

  <section class="page inner-right">
    <div class="process__photo" role="img" aria-label="High-rise residential tower with a regular grid of windows"></div>
    <div class="process">
      <h2 class="section-heading">PURCHASE<br>PROCESS</h2>
      <ol class="process__steps">
        <li class="process__step"><span class="process__num">1</span>Initial Contact</li>
        <li class="process__step"><span class="process__num">2</span>Property Evaluation</li>
        <li class="process__step"><span class="process__num">3</span>Offer Submission</li>
        <li class="process__step"><span class="process__num">4</span>Notarial Completion</li>
      </ol>
    </div>

    <div class="why">
      <h2 class="section-heading">WHY CHOOSE US</h2>
      <ul class="why__list">
        <li class="why__item">
          <span class="why__icon"><svg width="16" height="16" viewBox="0 0 16 16" fill="none" stroke="#24304a" stroke-width="1.6"><circle cx="8" cy="8" r="6"/><path d="M8 4.5V8l2.5 1.5"/></svg></span>
          <div><div class="why__title">Quick Transactions</div><div class="why__text">From first contact to notary in weeks</div></div>
        </li>
        <li class="why__item">
          <span class="why__icon"><svg width="16" height="16" viewBox="0 0 16 16" fill="none" stroke="#24304a" stroke-width="1.6"><rect x="3.5" y="7" width="9" height="6.5" rx="1"/><path d="M5.5 7V5a2.5 2.5 0 0 1 5 0v2"/></svg></span>
          <div><div class="why__title">Discreet Handling</div><div class="why__text">Confidential handling of every enquiry</div></div>
        </li>
        <li class="why__item">
          <span class="why__icon"><svg width="16" height="16" viewBox="0 0 16 16" fill="none" stroke="#24304a" stroke-width="1.8"><path d="M3.5 8.5l3 3 6-7"/></svg></span>
          <div><div class="why__title">No Bureaucracy</div><div class="why__text">Clear decisions, simple documentation</div></div>
        </li>
      </ul>
    </div>

    <div class="contact">
      <h2 class="section-heading">CONTACT US</h2>
      <ul class="contact__list">
        <li class="contact__item">
          <span class="contact__icon"><svg width="10" height="10" viewBox="0 0 10 10"><path d="M2 1h2l1 2.2-1.2.8a5 5 0 0 0 2.2 2.2l.8-1.2L9 6v2a1 1 0 0 1-1 1A7 7 0 0 1 1 2a1 1 0 0 1 1-1z" fill="#ffffff"/></svg></span>
          0284 119 4720
        </li>
        <li class="contact__item">
          <span class="contact__icon"><svg width="10" height="10" viewBox="0 0 10 10" fill="none" stroke="#ffffff" stroke-width="1.1"><rect x="1" y="2" width="8" height="6" rx=".6"/><path d="M1 2.5l4 3 4-3"/></svg></span>
          kontakt@torklumen-holding.de
        </li>
      </ul>
    </div>
  </section>

</body>
</html>
```